2 Page Web Design Project (coded)

What does the company do?
Pilot contracting, flying private/corporate jets.

What is its target market?
The target market is primarily the private jet management market, i.e. companies, which specialize in private aircraft management and are looking to fill crew positions on a short/long term basis, usually on short notice basis

How many pages should your website include?
2 Pages: 1/ Front Page with Company Logo, 2/ Services and Contact page

Do you want coding included? YES

Do you have any style you would like your website to have?
The main colors of my logo should be kept. Please see attached business card logo.

Other Instructions: Please see Veltraxa's website (media section) for Skyrunner 812 pictures for free download, which can be incorporated into the website. Link: http://www.veltraxa.example/en/aerospace/media-centre/multimedia-library/details?categoryID=L3-Veltraxa%20Skyrunner%20812%20Aircraft.

Please see www.midairstaffingdesk.example for services description.
Find attached source file business card and use loge design/font for website, so both business card and website are consistent.

Requirements
Must have
• email link to link to my personal email, without giving my email address.

```html
<!DOCTYPE html>
<html lang="en">
<head>
<meta charset="utf-8">
<title>Aerolane Crew Leasing Inc</title>
<link rel="stylesheet" href="https://fonts.googleapis.com/css2?family=Source+Sans+3:wght@400;600&display=swap">
<style>
  :root {
    --nav-bg: #231a12;
    --nav-active: #4a3b2e;
    --hero-bg: #35241a;
    --hero-map: #4a3b2f;
    --footer-bg: #21170f;
    --ink: #2b2520;
    --heading: #1f1a16;
    --white: #ffffff;
    --muted-link: #8a6d4f;
    --arrow: #8c8580;
    --arrow-dark: #2a2420;
  }
  * { box-sizing: border-box; margin: 0; padding: 0; }
  html, body { width: 1200px; height: 1062px; overflow: hidden; }
  body {
    font-family: "Source Sans 3", sans-serif;
    background: var(--white);
    color: var(--ink);
    position: relative;
  }

  .site-nav {
    position: absolute; left: 0; top: 0; width: 1200px; height: 68px;
    background: var(--nav-bg);
  }
  .site-nav ul { list-style: none; display: flex; height: 100%; padding-left: 24px; }
  .site-nav li { display: flex; }
  .site-nav a {
    display: flex; align-items: center; height: 100%;
    padding: 0 19px; color: var(--white); text-decoration: none;
    font-size: 17px; letter-spacing: 0.2px; text-transform: uppercase;
  }
  .site-nav li.is-active a { background: var(--nav-active); color: #1a140f; }

  .hero {
    position: absolute; left: 0; top: 68px; width: 1200px; height: 429px;
    background: var(--hero-bg);
  }
  .hero-map {
    position: absolute; left: 350px; top: 34px; width: 670px; height: 370px;
    border-radius: 46% 40% 44% 38% / 40% 44% 52% 46%;
    background: radial-gradient(ellipse at 50% 42%, var(--hero-map) 0%, #45352a 55%, rgba(69,53,42,0) 100%);
  }
  .brand {
    position: absolute; left: 29px; top: 236px;
    display: flex; align-items: center; gap: 18px;
  }
  .brand-mark { width: 24px; height: 24px; border-radius: 50%; background: var(--white); }
  .brand-name {
    display: flex; flex-direction: column; align-items: center;
    color: var(--white); font-weight: 400; text-transform: uppercase; line-height: 1;
  }
  .brand-name .brand-main { font-size: 54px; letter-spacing: 1.5px; }
  .brand-name .brand-sub { font-size: 15px; letter-spacing: 2px; margin-top: 12px; }

  .welcome { position: absolute; left: 24px; top: 518px; width: 624px; }
  .section-title {
    font-size: 24px; font-weight: 400; color: var(--heading);
    text-transform: uppercase; line-height: 30px; margin-bottom: 6px;
  }
  .welcome p { font-size: 15.6px; line-height: 23.6px; margin-bottom: 17px; }
  .view-more {
    display: block; text-align: right; color: var(--muted-link);
    font-size: 15px; text-decoration: none; margin-top: -4px;
  }

  .gallery { position: absolute; left: 689px; top: 518px; width: 490px; }
  .gallery-feature {
    position: absolute; left: 0; top: 41px; width: 490px; height: 275px;
    background: linear-gradient(180deg, #3f78b4 0%, #8fb6d8 45%, #d9e4ee 75%, #a9c2da 100%);
  }
  .gallery-thumbs { position: absolute; left: 0; top: 327px; width: 490px; height: 93px; }
  .thumb { position: absolute; top: 0; width: 105px; height: 93px; }
  .thumb-cabin { left: 18px; background: linear-gradient(135deg, #d8b98c, #6b3f22); }
  .thumb-flight { left: 135px; background: linear-gradient(180deg, #6f7a6a, #b8b8a8); }
  .thumb-ramp { left: 251px; background: linear-gradient(180deg, #8fb1d8, #c9d6e2 70%, #8a9aa8); }
  .thumb-seats { left: 367px; background: linear-gradient(135deg, #efe6d4, #b5946a); }
  .gallery-arrow { position: absolute; top: 36px; width: 12px; height: 20px; }
  .gallery-arrow.prev { left: 2px; }
  .gallery-arrow.next { left: 476px; }

  .site-footer {
    position: absolute; left: 0; top: 972px; width: 1200px; height: 90px;
    background: var(--footer-bg); color: var(--white);
  }
  .site-footer p { text-align: center; font-size: 12px; padding-top: 37px; }
  .site-footer a { color: var(--white); text-decoration: none; }
</style>
</head>
<body>
  <nav class="site-nav">
    <ul>
      <li class="is-active"><a href="#">Home</a></li>
      <li><a href="#">About Us</a></li>
      <li><a href="#">Products</a></li>
      <li><a href="#">Services &amp; Solutions</a></li>
      <li><a href="#">Suppliers</a></li>
      <li><a href="#">Corporate Responsibility</a></li>
      <li><a href="#">Media Centre</a></li>
      <li><a href="#">Careers</a></li>
    </ul>
  </nav>

  <header class="hero">
    <div class="hero-map" role="img" aria-label="Faint world map spread across the brown banner"></div>
    <div class="brand">
      <span class="brand-mark"></span>
      <span class="brand-name">
        <span class="brand-main">Aerolane Crew</span>
        <span class="brand-sub">Leasing Inc</span>
      </span>
    </div>
  </header>

  <main>
    <section class="welcome">
      <h1 class="section-title">Welcome to Aerolane Crew</h1>
      <p>Lorem Ipsum is simply dummy text of the printing and typesetting industry. Lorem Ipsum has been the industry's standard dummy text ever since the 1500s, when an unknown printer took a galley of type and scrambled it to make a type specimen book. It has survived not only five centuries, but also the leap into electronic typesetting, remaining essentially unchanged. It was popularised in the 1960s with the release of Setwell sheets containing Lorem Ipsum passages, and more recently with desktop publishing software like Pagemill Studio including versions of Lorem Ipsum.</p>
      <p>Lorem Ipsum is simply dummy text of the printing and typesetting industry. Lorem Ipsum has been the industry's standard dummy text ever since the 1500s, when an unknown printer took a galley of type and scrambled it to make a type specimen book. It has survived not only five centuries, but also the leap into electronic typesetting, remaining essentially unchanged. It was popularised in the 1960s with the release of Setwell sheets containing Lorem Ipsum passages, and more recently with desktop publishing software like Pagemill Studio including versions of Lorem Ipsum.</p>
      <a class="view-more" href="#">view more</a>
    </section>

    <section class="gallery">
      <h2 class="section-title">Photo&nbsp; Gallery</h2>
      <div class="gallery-feature" role="img" aria-label="Business jet flying above the clouds in a blue sky"></div>
      <div class="gallery-thumbs">
        <svg class="gallery-arrow prev" viewBox="0 0 12 20" aria-label="Previous"><path d="M10 2 L3 10 L10 18" fill="none" stroke="var(--arrow)" stroke-width="2.5"/></svg>
        <div class="thumb thumb-cabin" role="img" aria-label="Jet cabin with wooden table and leather seats"></div>
        <div class="thumb thumb-flight" role="img" aria-label="Business jet flying over land"></div>
        <div class="thumb thumb-ramp" role="img" aria-label="Business jet parked on a wet ramp"></div>
        <div class="thumb thumb-seats" role="img" aria-label="Cream leather cabin seats"></div>
        <svg class="gallery-arrow next" viewBox="0 0 12 20" aria-label="Next"><path d="M2 2 L9 10 L2 18" fill="none" stroke="var(--arrow-dark)" stroke-width="2.5"/></svg>
      </div>
    </section>
  </main>

  <footer class="site-footer">
    <p>© 2012 &nbsp;- <a href="#">Terms of Service</a> - <a href="#">Privacy Policy</a> - <a href="#">Program Policies</a></p>
  </footer>
</body>
</html>
```